Building company buisness cards

We are looking for a sharp modern new look for our business cards.
We are a New Zealand based company that specialises in house and land packages.
We have attached a photo of the current logo and would like to see if it can be improved somehow if needed.
We are open to any colours but we have chosen green at this stage.
Feel free to change the font and make the logo smarter looking.
Play with the colours and see what looks best.

We want a card that looks so good know one will want to throw it away!

Target Market(s)

Home buyers

Industry/Entity Type

Building

Contact Information for Business Card

Derek Tolvane
0217394062
dtolvane@quillmarkhomesteads.co.nz
quillmarkhomesteads.co.nz

Font styles to use
Serif
Sans Serif

Colors

Designer to choose colors to be used in the design.

Requirements
Must have
• Logo and company name on one side, details on the other side
Nice to have
• Color codes for the original green are HEX #4a8028, RGB(74,128,40), CMYK(42,0,69,50)
• Round corners, Raised and/or spot UV

```html
<!DOCTYPE html>
<html lang="en">
<head>
<meta charset="utf-8">
<title>Quillmark Homesteads – Business Cards</title>
<link href="https://fonts.googleapis.com/css2?family=Open+Sans:wght@400;700;800&display=swap" rel="stylesheet">
<style>
  :root{
    --brand-green:#4a8a22;
    --brand-green-dark:#3d7a1a;
    --card-white:#ffffff;
    --stage:#e6e7e4;
    --rule:#d8d8d8;
    --shadow:rgba(0,0,0,.18);
  }
  *{box-sizing:border-box;margin:0;padding:0}
  html,body{width:1200px;height:900px;overflow:hidden}
  body{background:var(--stage);font-family:"Open Sans",Arial,sans-serif;position:relative}

  .card{
    position:absolute;left:290px;width:620px;height:354px;
    border-radius:22px;background:var(--card-white);overflow:hidden;
    box-shadow:0 10px 28px var(--shadow);
  }
  .card--front{top:72px}
  .card--back{top:474px}

  /* wordmark */
  .wordmark{display:flex;align-items:center;gap:12px;color:var(--brand-green)}
  .wordmark__dot{width:16px;height:16px;border-radius:50%;background:var(--brand-green);flex:none}
  .wordmark__name{font-weight:800;line-height:.95;letter-spacing:-.5px}
  .wordmark__rule{display:block;height:1px;background:var(--rule);margin-top:8px}

  /* front */
  .front__brand{position:absolute;left:0;top:0;width:268px;height:100%;display:flex;align-items:center;justify-content:center}
  .front__brand .wordmark__name{font-size:28px}
  .front__brand .wordmark__rule{width:56px;margin-left:60px}

  .front__panel{position:absolute;left:280px;top:0;right:0;bottom:0;background:var(--brand-green);color:#fff;padding:84px 24px 0 44px}
  .front__tab{position:absolute;left:268px;top:150px;width:24px;height:118px;background:var(--brand-green-dark);border-radius:3px 0 0 3px;box-shadow:-2px 2px 4px rgba(0,0,0,.15)}
  .person__name{font-size:24px;font-weight:700;line-height:1.1}
  .person__title{font-size:17px;font-weight:400;margin:2px 0 18px}
  .contact{list-style:none}
  .contact__item{display:flex;align-items:center;gap:9px;font-size:13px;line-height:1.85;white-space:nowrap}
  .contact__icon{width:12px;height:12px;flex:none}

  /* back */
  .back__brand{position:absolute;inset:0;display:flex;align-items:center;justify-content:center}
  .back__brand .wordmark__name{font-size:44px}
  .back__brand .wordmark__rule{width:70px;margin-left:120px}
</style>
</head>
<body>

<section class="card card--front" aria-label="Business card front">
  <div class="front__brand">
    <div class="wordmark">
      <span class="wordmark__dot"></span>
      <div>
        <p class="wordmark__name">quillmark<br>homesteads.</p>
        <span class="wordmark__rule"></span>
      </div>
    </div>
  </div>
  <div class="front__panel">
    <p class="person__name">Derek Tolvane</p>
    <p class="person__title">President</p>
    <ul class="contact">
      <li class="contact__item">
        <svg class="contact__icon" viewBox="0 0 12 12"><path d="M3 1 L5 3.5 L4 5 Q5 7 7 8 L8.5 7 L11 9 L9.5 11 Q4 10.5 1 3 Z" fill="#fff"/></svg>
        0217394062
      </li>
      <li class="contact__item">
        <svg class="contact__icon" viewBox="0 0 12 12"><rect x="0.5" y="2.5" width="11" height="7" fill="#fff"/><path d="M0.5 2.5 L6 6.5 L11.5 2.5" fill="none" stroke="#4a8a22" stroke-width="1"/></svg>
        dtolvane@quillmarkhomesteads.co.nz
      </li>
      <li class="contact__item">
        <svg class="contact__icon" viewBox="0 0 12 12" fill="none" stroke="#fff" stroke-width="1.2"><circle cx="6" cy="6" r="5"/><ellipse cx="6" cy="6" rx="2.2" ry="5"/><path d="M1 6h10"/></svg>
        www.quillmarkhomesteads.co.nz
      </li>
    </ul>
  </div>
  <span class="front__tab"></span>
</section>

<section class="card card--back" aria-label="Business card back">
  <div class="back__brand">
    <div class="wordmark">
      <span class="wordmark__dot"></span>
      <div>
        <p class="wordmark__name">quillmark<br>homesteads.</p>
        <span class="wordmark__rule"></span>
      </div>
    </div>
  </div>
</section>

</body>
</html>
```